Psychology and personal development service needs an awesome Web Design

Hi, we are Bright, Build & Bloom, a psychology and personal development service located in Melbourne Australia. We already have a website www.brightbuild&bloom.org but it is in great need of a makeover! We add to the website regularly with articles and so we need a space to archive these when they come off the main page, and we have products that we would like to sell internationally so we need a shop page that can convert currencies for international sales and calculate postage and handling. We have a Circlebook page that we would like to link as well as a newsletter that we would like to archive on the website. We have just had a logo designed through sketch hive and would like to incorporate this into our website. We want something with high visual impact and uncluttered.
We also run workshops and events so need a tab for this.
Thanks for getting on board!

```html
<!DOCTYPE html>
<html lang="en">
<head>
<meta charset="utf-8">
<title>Bright, Build &amp; Bloom — Psychology and Personal Development Center</title>
<link rel="stylesheet" href="https://fonts.googleapis.com/css2?family=Oswald:wght@400;500&family=Open+Sans:wght@400;600&family=Questrial&display=swap">
<style>
:root{
  --purple:#6b4a9c;
  --purple-deep:#5a3d8a;
  --teal:#33b9a0;
  --pink:#e0409a;
  --white:#ffffff;
  --paper:#f7f7f7;
  --ink:#444444;
  --muted:#7a7a7a;
  --line:#e4e4e4;
  --grey-box:#6f6f6f;
  --night:#0d0d0d;
  --star:#f2a81d;
}
*{box-sizing:border-box;margin:0;padding:0}
html,body{width:1200px;height:2239px;overflow:hidden}
body{background:var(--purple);font-family:"Open Sans",Arial,sans-serif;color:var(--ink);position:relative}
.page{position:absolute;left:73px;top:51px;width:1054px;height:2188px;background:var(--paper)}
.abs{position:absolute}

/* header */
.site-header{left:0;top:0;width:1054px;height:162px;background:var(--white)}
.brand{left:26px;top:52px;display:flex;align-items:center;gap:14px}
.brand-dot{width:52px;height:52px;border-radius:50%;background:var(--purple)}
.brand-name{font-family:"Questrial",sans-serif;font-size:27px;color:var(--purple)}
.contact-phone-icon{left:768px;top:30px}
.contact-lines{left:828px;top:30px;font-family:"Questrial",sans-serif;font-size:15px;line-height:24px;color:var(--purple-deep);white-space:nowrap}
.header-rule{left:360px;top:97px;width:667px;height:1px;background:var(--line)}
.main-nav{left:361px;top:121px;display:flex;font-family:"Questrial",sans-serif;font-size:14px;color:#333}
.main-nav span{position:absolute;white-space:nowrap}
.main-nav .current{color:var(--purple)}

/* hero */
.hero{left:0;top:162px;width:1054px;height:547px;overflow:hidden}
.hero-art{position:absolute;inset:0;background:radial-gradient(ellipse at 25% 40%,#4f88d8 0%,#1a3e8e 30%,#0a1a4f 60%,#050b26 100%)}
.hero-copy{left:581px;top:189px;color:var(--white);font-family:"Oswald",sans-serif;white-space:nowrap}
.hero-kicker{font-size:30px;letter-spacing:1px;line-height:40px}
.hero-title{font-size:44px;line-height:62px;font-weight:500;margin-top:4px}
.hero-dots{left:583px;top:429px;display:flex;gap:10px}
.hero-dots i{width:24px;height:24px;border-radius:50%;background:rgba(255,255,255,.25)}

/* books */
.book-card{top:746px;width:232px;height:415px;background:var(--white);border:1px solid #ececec}
.book-cover{width:232px;height:273px}
.book-title{position:absolute;left:15px;top:290px;font-size:14px;color:#555;white-space:nowrap}
.book-desc{position:absolute;left:15px;top:318px;width:205px;font-size:11px;line-height:19px;color:#666;text-align:justify}
.book-price{position:absolute;left:15px;top:384px;font-size:11px;color:#555;display:flex;align-items:center;gap:10px}
.sketch{left:796px;top:746px;width:232px;height:415px;background:linear-gradient(180deg,#fbfbfb,#eeeeee)}

/* promo band */
.promo{left:0;top:1200px;width:1054px;height:197px;background:var(--teal);text-align:center;color:var(--white);font-family:"Questrial",sans-serif}
.promo h2{font-weight:400;font-size:26px;margin-top:28px;letter-spacing:.2px}
.promo p{font-size:16px;margin-top:8px}
.promo-button{display:inline-block;margin-top:22px;width:364px;height:47px;line-height:47px;border-radius:24px;background:var(--purple);font-size:19px;box-shadow:0 3px 0 rgba(0,0,0,.15)}

/* articles */
.section-title{font-family:"Questrial",sans-serif;font-weight:400;font-size:19px;color:#444;letter-spacing:.3px}
.article{left:25px;width:660px;height:168px}
.article-thumb{position:absolute;left:0;top:0;width:163px;height:167px}
.article-title{position:absolute;left:190px;top:0;font-size:15px;color:#444}
.article-meta{position:absolute;left:190px;top:29px;font-size:11px;color:#555;display:flex;gap:24px}
.stars{color:var(--star);letter-spacing:1px}
.stars b{color:#ccc;font-weight:400}
.article-text{position:absolute;left:190px;top:55px;width:458px;font-size:10.5px;line-height:19px;color:#777}
.learn-more{position:absolute;left:187px;top:142px;width:103px;height:27px;border-radius:3px;background:var(--pink);color:var(--white);font-size:10px;line-height:27px;padding-left:10px}

/* events */
.event{left:718px;width:309px;height:120px}
.event-date{position:absolute;left:0;top:0;width:34px;height:62px;background:var(--teal);color:var(--white);text-align:center;font-family:"Oswald",sans-serif}
.event-date .day{font-size:19px;line-height:30px;display:block;margin-top:2px}
.event-date .mon{font-size:12px}
.event-tag{position:absolute;left:0;top:62px;width:34px;height:37px;background:var(--grey-box)}
.event-title{position:absolute;left:72px;top:0;font-size:15px;color:#666}
.event-sub{position:absolute;left:72px;top:29px;font-size:11px;color:var(--purple)}
.event-text{position:absolute;left:72px;top:55px;width:237px;font-size:10.5px;line-height:19px;color:#888;text-align:justify}

.social-box{left:718px;top:1749px;width:309px;height:290px;background:var(--white);border:1px solid #dcdcdc}
.social-head{height:39px;background:#f3f3f3;border-bottom:1px solid #dcdcdc;font-size:12px;line-height:39px;padding-left:14px;color:#444}
.social-ctrl{position:absolute;top:10px;width:20px;height:20px;border:1px solid #bbb;background:#fafafa}
.social-row{position:absolute;left:14px;display:flex;gap:14px}
.social-avatar{width:46px;height:46px;border-radius:50%;background:var(--purple)}
.social-name{font-size:11px;color:var(--purple-deep)}
.like-btn{display:inline-block;margin-top:6px;width:38px;height:16px;background:#4a63a3;border-radius:2px}
.like-count{font-size:10px;color:#777;margin-left:4px}
.post-text{font-size:10.5px;line-height:20px;color:#444;width:200px}

/* footer */
.site-footer{left:0;top:2077px;width:1054px;height:111px;background:var(--night);color:#8a8a8a}
.copyright{position:absolute;left:31px;top:32px;font-size:10px}
.footer-links{position:absolute;left:31px;top:64px;font-size:10px}
.footer-social{position:absolute;left:540px;top:45px;display:flex;gap:8px}
.footer-social i{width:24px;height:24px;border-radius:50%}
.newsletter-label{position:absolute;left:749px;top:24px;font-size:13px;color:#bbb}
.newsletter-input{position:absolute;left:749px;top:53px;width:187px;height:31px;border:1px solid #333;font-size:11px;line-height:29px;padding-left:12px;color:#ccc}
.subscribe{position:absolute;left:948px;top:53px;width:77px;height:31px;background:var(--pink);color:var(--white);font-size:12px;line-height:31px;text-align:center;border-radius:2px}
</style>
</head>
<body>
<div class="page">

  <header class="site-header abs">
    <div class="brand abs">
      <span class="brand-dot"></span>
      <span class="brand-name">Bright, Build &amp; Bloom</span>
    </div>
    <svg class="contact-phone-icon abs" width="30" height="38" viewBox="0 0 30 38" aria-hidden="true">
      <path d="M6 2 L12 2 L14 10 L10 13 Q13 22 19 27 L23 24 L29 28 L28 35 Q20 38 11 28 Q2 18 3 6 Z" fill="#bdbdbd"/>
    </svg>
    <div class="contact-lines abs">info@brightbuildandbloom.org<br>+900.214.5580</div>
    <div class="header-rule abs"></div>
    <nav class="main-nav abs">
      <span class="current" style="left:0">HOME</span>
      <span style="left:73px">ABOUT US</span>
      <span style="left:175px">BOOKS</span>
      <span style="left:256px">PRODUCTS</span>
      <span style="left:361px">ONLINE STORE</span>
      <span style="left:493px">EVENTS</span>
      <span style="left:576px">CONTACT US</span>
    </nav>
  </header>

  <section class="hero abs">
    <div class="hero-art" role="img" aria-label="Glowing blue human head in profile with an illuminated brain, set against a dark blue circuit-board pattern"></div>
    <div class="hero-copy abs">
      <div class="hero-kicker">BRIGHT, BUILD &amp; BLOOM</div>
      <div class="hero-title">Psychology and Personal<br>Development Center</div>
    </div>
    <div class="hero-dots abs"><i></i><i></i></div>
  </section>

  <article class="book-card abs" style="left:25px">
    <div class="book-cover" role="img" aria-label="Book cover for Willow, sepia portrait of a young woman" style="background:linear-gradient(135deg,#5a4a3a,#2e241c)"></div>
    <div class="book-title">Willow - My Father Was a Monk</div>
    <p class="book-desc">Seventeen-year-old Willow is on a search for identity and transformation as she attempts to come to terms</p>
    <div class="book-price"><svg width="16" height="14" viewBox="0 0 16 14"><path d="M0 1h3l2 8h8l2-6H5" fill="none" stroke="#e0409a" stroke-width="1.6"/><circle cx="6" cy="12" r="1.4" fill="#e0409a"/><circle cx="12" cy="12" r="1.4" fill="#e0409a"/></svg>$ 15.00</div>
  </article>

  <article class="book-card abs" style="left:282px">
    <div class="book-cover" role="img" aria-label="Book cover for Anchored, sepia photograph of an old clock tower" style="background:linear-gradient(180deg,#cbb99a,#7a6446)"></div>
    <div class="book-title">Willow - My Father Was a Monk</div>
    <p class="book-desc">Seventeen-year-old Willow is on a search for identity and transformation as she attempts to come to terms</p>
    <div class="book-price"><svg width="16" height="14" viewBox="0 0 16 14"><path d="M0 1h3l2 8h8l2-6H5" fill="none" stroke="#e0409a" stroke-width="1.6"/><circle cx="6" cy="12" r="1.4" fill="#e0409a"/><circle cx="12" cy="12" r="1.4" fill="#e0409a"/></svg>$ 15.00</div>
  </article>

  <article class="book-card abs" style="left:539px">
    <div class="book-cover" role="img" aria-label="Book cover for A Small Book of Dawn, pale blue with a seashell" style="background:linear-gradient(180deg,#8fc3ee,#6aa6dc)"></div>
    <div class="book-title">Willow - My Father Was a Monk</div>
    <p class="book-desc">Seventeen-year-old Willow is on a search for identity and transformation as she attempts to come to terms</p>
    <div class="book-price"><svg width="16" height="14" viewBox="0 0 16 14"><path d="M0 1h3l2 8h8l2-6H5" fill="none" stroke="#e0409a" stroke-width="1.6"/><circle cx="6" cy="12" r="1.4" fill="#e0409a"/><circle cx="12" cy="12" r="1.4" fill="#e0409a"/></svg>$ 15.00</div>
  </article>

  <div class="sketch abs" role="img" aria-label="Pencil sketch of a girl holding a large seashell"></div>

  <section class="promo abs">
    <h2>NEW BOOK - SEQUEL TO ANCHORED AVAILABLE FOR PURCHASE</h2>
    <p>Co-founder of Bright, Build &amp; Bloom, Hannah Morrow, has just released the sequel to Anchored</p>
    <span class="promo-button">Click here for further details on Willow</span>
  </section>

  <h3 class="section-title abs" style="left:24px;top:1425px">LATEST ARTICLES</h3>

  <article class="article abs" style="top:1476px">
    <div class="article-thumb" role="img" aria-label="Glowing blue brain with a heartbeat line" style="background:radial-gradient(circle at 50% 45%,#49a8ff,#0b2a66 75%)"></div>
    <div class="article-title">Easing Pain Within The Physical Body</div>
    <div class="article-meta"><span class="stars">★★★<b>☆☆</b></span><span>May 2014</span></div>
    <p class="article-text">We spend much of our lives directing our life force and our energy out into the world. We focus on people, things and environments that are external to ourselves. At some point if we lack balance between an external focus and an internal one, our bodies and minds begin to suffer the effects through exhaustion and injury and illness.</p>
    <span class="learn-more">LEARN MORE ➜</span>
  </article>

  <article class="article abs" style="top:1673px">
    <div class="article-thumb" role="img" aria-label="Blue network of glowing lines shaped like a brain" style="background:radial-gradient(circle at 50% 50%,#5a7fe0,#13206a 75%)"></div>
    <div class="article-title">My Power Doesn't Understand</div>
    <div class="article-meta"><span class="stars">★★★<b>☆☆</b></span><span>May 2014</span></div>
    <p class="article-text">We spend much of our lives directing our life force and our energy out into the world. We focus on people, things and environments that are external to ourselves. At some point if we lack balance between an external focus and an internal one, our bodies and minds begin to suffer the effects through exhaustion and injury and illness.</p>
    <span class="learn-more">LEARN MORE ➜</span>
  </article>

  <article class="article abs" style="top:1870px">
    <div class="article-thumb" role="img" aria-label="Therapist treating a patient in a bright clinic" style="background:linear-gradient(135deg,#4a3a34,#d9c8c4 55%,#f0e6e8)"></div>
    <div class="article-title">Easing Pain Within The Physical Body</div>
    <div class="article-meta"><span class="stars">★★★<b>☆☆</b></span><span>May 2014</span></div>
    <p class="article-text">We spend much of our lives directing our life force and our energy out into the world. We focus on people, things and environments that are external to ourselves. At some point if we lack balance between an external focus and an internal one, our bodies and minds begin to suffer the effects through exhaustion and injury and illness.</p>
    <span class="learn-more">LEARN MORE ➜</span>
  </article>

  <h3 class="section-title abs" style="left:718px;top:1425px">UPCOMING EVENTS</h3>

  <article class="event abs" style="top:1474px">
    <div class="event-date"><span class="day">30</span><span class="mon">Oct</span></div>
    <div class="event-tag"><svg width="34" height="37" viewBox="0 0 34 37"><path d="M10 12h14v9h-8l-4 3v-3h-2z" fill="#fff"/></svg></div>
    <div class="event-title">Simplicity Leads to Good Health</div>
    <div class="event-sub">My Father Was a Monk</div>
    <p class="event-text">Morbi tempor quam vel massa adi piscing ute cursus mi congue pelle ntesque niselit er comte Morbi tempor quam vel</p>
  </article>

  <article class="event abs" style="top:1611px">
    <div class="event-date"><span class="day">30</span><span class="mon">Oct</span></div>
    <div class="event-tag"><svg width="34" height="37" viewBox="0 0 34 37"><path d="M10 12h14v9h-8l-4 3v-3h-2z" fill="#fff"/></svg></div>
    <div class="event-title">Simplicity Leads to Good Health</div>
    <div class="event-sub">My Father Was a Monk</div>
    <p class="event-text">Morbi tempor quam vel massa adi piscing ute cursus mi congue pelle ntesque niselit er comte Morbi tempor quam vel</p>
  </article>

  <aside class="social-box abs">
    <div class="social-head">FIND US ON CIRCLEBOOK</div>
    <span class="social-ctrl" style="left:220px"></span>
    <span class="social-ctrl" style="left:242px"></span>
    <span class="social-ctrl" style="left:264px"></span>
    <div class="social-row" style="top:56px">
      <span class="social-avatar"></span>
      <div><div class="social-name">Bright, Build &amp; Bloom</div><span class="like-btn"></span><span class="like-count">60</span></div>
    </div>
    <div style="position:absolute;left:0;top:116px;width:307px;height:1px;background:var(--line)"></div>
    <div class="social-row" style="top:134px">
      <span class="social-avatar"></span>
      <div>
        <div style="font-size:10px;color:#333">BRIGHT, BUILD &amp; BLOOM</div>
        <div style="font-size:10px;color:#555;margin-top:4px">7 HRS</div>
        <p class="post-text" style="margin-top:6px">Courage; We do not find courage by looking to others but by looking into ourselves when we see the horror that surrounds us. Look past this into our experience and grow within our</p>
      </div>
    </div>
  </aside>

  <footer class="site-footer abs">
    <div class="copyright">©2014 Bright, Build &amp; Bloom , All Rights Reserved.</div>
    <div class="footer-links">Home &nbsp;/&nbsp; About Us &nbsp;/&nbsp; Books &nbsp;/&nbsp; Products &nbsp;/&nbsp; Online Store &nbsp;/&nbsp; Events &nbsp;/&nbsp; Contact Us</div>
    <div class="footer-social"><i style="background:#3b5a9a"></i><i style="background:#2a9fd8"></i><i style="background:#c8302a"></i></div>
    <div class="newsletter-label">Newsletter Sign Up</div>
    <div class="newsletter-input">Enter Your Email</div>
    <div class="subscribe">Subscribe</div>
  </footer>

</div>
</body>
</html>
```